Suite Refresh Partners - Tabletop Display

We need a 5'x5' trade show display for a hotel renovation company named "Suite Refresh Partners." Suite Refresh Partners is the most complete authority on hotel renovation in the country, and we're the only 100% turn-key renovator in Colorado. With one phone call, we deliver an approved design, FF&E purchasing, logistics, construction, installation, and warranty administration. The design needs to convey professionalism. Our goal is to help our clients reduce costs and reduce stress while achieving the best results. The colors should align with the attached brochure for our Raleigh office.

Target Market(s)

Hotel owners and general managers

Industry/Entity Type

Design Agency

Colors
3277b5
85acd3
cfdeed

Requirements
Must have
• Our product is a blend of design and construction. I need to convey our services and attention to detail without seeming salesy, bold, or aggressive. The goal is to convey confidence and help to relax our potential client base.
Nice to have
• Possibly one or more photos of completed projects. Not sure if exterior, lobby, or guest room photos would be best. I can send files via dropbox if that's helpful.
Should not have
• I've included a photo of the old display at a trade show. I strongly dislike the yellow and red on the display. Please try to stick to the color palette of the attached brochure.

```html
<!DOCTYPE html>
<html lang="en">
<head>
<meta charset="utf-8">
<title>Suite Refresh Partners – Turn-Key Renovations</title>
<link rel="stylesheet" href="https://fonts.googleapis.com/css2?family=Montserrat:wght@600;800&family=Raleway:wght@200;300&family=Exo+2:wght@500&display=swap">
<style>
  :root {
    --brand-blue: #2f74b5;
    --brand-blue-deep: #1f5f9f;
    --brand-blue-light: #85acd3;
    --brand-blue-pale: #cfdeed;
    --band-black: #1a1a1a;
    --band-charcoal: #3a3a3a;
    --band-grey: #7b7b7b;
    --paper: #ffffff;
  }
  html, body {
    margin: 0;
    padding: 0;
    width: 1200px;
    height: 1200px;
    overflow: hidden;
    background: var(--paper);
  }
  .display {
    position: relative;
    width: 1200px;
    height: 1200px;
    overflow: hidden;
    background: var(--paper);
  }
  .display-shapes {
    position: absolute;
    inset: 0;
    width: 1200px;
    height: 1200px;
  }
  .brand-name {
    position: absolute;
    left: 54px;
    top: 62px;
    margin: 0;
    font-family: "Montserrat", sans-serif;
    font-weight: 600;
    font-size: 50px;
    line-height: 1.06;
    color: var(--brand-blue);
    letter-spacing: 0.3px;
  }
  .headline {
    position: absolute;
    left: 566px;
    top: 60px;
    margin: 0;
    color: var(--brand-blue);
  }
  .headline-kicker {
    display: block;
    font-family: "Montserrat", sans-serif;
    font-weight: 800;
    font-size: 56px;
    line-height: 1;
    letter-spacing: 1px;
  }
  .headline-main {
    display: block;
    margin-top: 12px;
    font-family: "Raleway", sans-serif;
    font-weight: 300;
    font-size: 86px;
    line-height: 1;
    letter-spacing: -0.5px;
  }
  .tagline-box {
    position: absolute;
    left: 14px;
    top: 871px;
    width: 698px;
    height: 93px;
    background: var(--paper);
  }
  .tagline {
    position: absolute;
    left: 83px;
    top: 9px;
    margin: 0;
    font-family: "Raleway", sans-serif;
    font-weight: 200;
    font-size: 62px;
    line-height: 1.2;
    color: var(--brand-blue);
    white-space: nowrap;
  }
  .service-list {
    position: absolute;
    top: 1012px;
    margin: 0;
    padding: 0;
    list-style: none;
    font-family: "Exo 2", sans-serif;
    font-weight: 500;
    font-size: 31px;
    line-height: 45px;
    color: var(--paper);
  }
  .service-list--first { left: 60px; }
  .service-list--second { left: 314px; }
  .service-list li {
    position: relative;
    padding-left: 35px;
    white-space: nowrap;
  }
  .service-list li::before {
    content: "";
    position: absolute;
    left: 0;
    top: 15px;
    width: 0;
    height: 0;
    border-left: 17px solid transparent;
    border-bottom: 17px solid var(--paper);
  }
  .inset-frame {
    position: absolute;
    left: 831px;
    top: 823px;
    width: 325px;
    height: 324px;
    background: var(--paper);
    box-shadow: 0 2px 6px rgba(0, 0, 0, 0.18);
  }
  .inset-photo {
    position: absolute;
    left: 10px;
    top: 10px;
    width: 305px;
    height: 304px;
    background:
      radial-gradient(ellipse 70% 40% at 70% 78%, rgba(255, 214, 150, 0.55), rgba(255, 214, 150, 0) 70%),
      linear-gradient(180deg, #7a8fb0 0%, #a6aec0 22%, #c9925a 48%, #b46c3c 68%, #6e5444 84%, #cfcac0 100%);
  }
</style>
</head>
<body>
<main class="display">
  <svg class="display-shapes" viewBox="0 0 1200 1200" xmlns="http://www.w3.org/2000/svg">
    <defs>
      <linearGradient id="lobbyBase" x1="0" y1="0" x2="0" y2="1">
        <stop offset="0" stop-color="#d9a866"/>
        <stop offset="0.5" stop-color="#c9a27a"/>
        <stop offset="0.78" stop-color="#8e6a4c"/>
        <stop offset="1" stop-color="#4e3424"/>
      </linearGradient>
      <radialGradient id="lobbyWarmLight" cx="0.72" cy="0.25" r="0.55">
        <stop offset="0" stop-color="#f6d08a" stop-opacity="0.85"/>
        <stop offset="1" stop-color="#f6d08a" stop-opacity="0"/>
      </radialGradient>
      <radialGradient id="lobbyStoneShade" cx="0.25" cy="0.45" r="0.4">
        <stop offset="0" stop-color="#5d4a3c" stop-opacity="0.75"/>
        <stop offset="1" stop-color="#5d4a3c" stop-opacity="0"/>
      </radialGradient>
      <radialGradient id="lobbySeatingGlow" cx="0.6" cy="0.78" r="0.4">
        <stop offset="0" stop-color="#e6d6c2" stop-opacity="0.7"/>
        <stop offset="1" stop-color="#e6d6c2" stop-opacity="0"/>
      </radialGradient>
      <linearGradient id="diagonalBand" x1="0" y1="1" x2="1" y2="0">
        <stop offset="0" stop-color="var(--band-charcoal)"/>
        <stop offset="1" stop-color="var(--band-black)"/>
      </linearGradient>
      <linearGradient id="footerBand" x1="0" y1="0" x2="1" y2="0">
        <stop offset="0" stop-color="#2f78b8"/>
        <stop offset="1" stop-color="#2a6fb0"/>
      </linearGradient>
    </defs>

    <g class="lobby-photo" role="img" aria-label="Photo of a renovated hotel lobby with stone fireplace, pendant chandelier and lounge seating">
      <polygon points="430,244 1200,244 1200,986 8,986" fill="url(#lobbyBase)"/>
      <polygon points="430,244 1200,244 1200,986 8,986" fill="url(#lobbyWarmLight)"/>
      <polygon points="430,244 1200,244 1200,986 8,986" fill="url(#lobbyStoneShade)"/>
      <polygon points="430,244 1200,244 1200,986 8,986" fill="url(#lobbySeatingGlow)"/>
    </g>

    <polygon class="accent-veil" points="1200,540 1200,986 880,986" fill="var(--brand-blue)" opacity="0.5"/>
    <polygon class="accent-veil-soft" points="1200,620 1200,986 980,986" fill="var(--brand-blue-deep)" opacity="0.35"/>

    <polygon class="diagonal-band" points="415,129 495,129 8,986 0,986 0,853" fill="url(#diagonalBand)"/>
    <polygon class="diagonal-band-grey" points="495,129 560,244 430,244" fill="var(--band-grey)"/>

    <rect class="footer-band" x="0" y="986" width="1200" height="214" fill="url(#footerBand)"/>
    <polygon class="footer-facet" points="1200,940 1200,1200 1010,1200" fill="var(--brand-blue-deep)" opacity="0.6"/>
    <polygon class="footer-facet-light" points="1200,1010 1200,1200 1110,1200" fill="var(--brand-blue-light)" opacity="0.25"/>
  </svg>

  <h2 class="brand-name">Suite<br>Refresh<br>Partners</h2>

  <h1 class="headline">
    <span class="headline-kicker">TURN-KEY</span>
    <span class="headline-main">RENOVATIONS</span>
  </h1>

  <div class="tagline-box">
    <p class="tagline">Everything Included!</p>
  </div>

  <ul class="service-list service-list--first">
    <li>Design</li>
    <li>FF&amp;E</li>
    <li>Purchasing</li>
    <li>Logistics</li>
  </ul>
  <ul class="service-list service-list--second">
    <li>Construction</li>
    <li>Installation</li>
    <li>Warranty administration</li>
  </ul>

  <div class="inset-frame">
    <div class="inset-photo" role="img" aria-label="Photo of a renovated hotel exterior at dusk with covered entrance"></div>
  </div>
</main>
</body>
</html>
```